Upmarket Dessert Lounge needs a Business Card Design

We are an upmarket dessert lounge needing a business card to match our image.

We want something that is simple yet beautiful, feminine, classy, sophisticated and elegant. We want it to stand out and don't mind if it is bold.

The design should include our logo and colours of red or maroon with gold highlights. We don't mind if black is used.

Marlow & Quince

Target Market(s)

For those who like to indulge or treat themselves and give in to their temptations on good quality desserts.

Industry/Entity Type

Business

Requirements
Must have
• Must include our logo and our name

Marlow & Quince

M & Q

```html
<!DOCTYPE html>
<html lang="en">
<head>
<meta charset="utf-8">
<title>Marlow &amp; Quince — Business Card</title>
<link rel="stylesheet" href="https://fonts.googleapis.com/css2?family=Source+Sans+3:wght@400;600&display=swap">
<style>
  :root {
    --stage: #d9d9d9;
    --card: #000000;
    --maroon: #7b1517;
    --gold: #f5c27e;
    --cream: #f8d7a4;
    --white: #ffffff;
    --shadow: rgba(0, 0, 0, 0.35);
  }
  html, body {
    margin: 0;
    padding: 0;
    width: 956px;
    height: 1200px;
    overflow: hidden;
    background: var(--stage);
  }
  .stage {
    position: relative;
    width: 956px;
    height: 1200px;
    font-family: "Source Sans 3", "Myriad Pro", Arial, sans-serif;
  }
  .card {
    position: absolute;
    width: 797px;
    height: 455px;
    background: var(--card);
    border-radius: 28px;
    box-shadow: 0 6px 14px var(--shadow);
    color: var(--white);
    text-align: center;
  }
  .card--front { left: 80px; top: 115px; }
  .card--back  { left: 74px; top: 632px; }

  .brand {
    position: absolute;
    left: 0;
    right: 0;
    display: flex;
    align-items: center;
    justify-content: center;
    color: var(--cream);
    font-weight: 400;
    letter-spacing: 0.04em;
    line-height: 1;
  }
  .brand__mark {
    display: block;
    flex: none;
    background: var(--maroon);
  }
  .card--front .brand {
    top: 108px;
    height: 44px;
    gap: 16px;
    font-size: 42px;
  }
  .card--front .brand__mark { width: 34px; height: 34px; }
  .card--back .brand {
    top: 183px;
    height: 100px;
    gap: 30px;
    font-size: 100px;
  }
  .card--back .brand__mark { width: 76px; height: 76px; }

  .holder {
    position: absolute;
    top: 268px;
    left: 0;
    right: 0;
    margin: 0;
    font-size: 26px;
    line-height: 36px;
    color: var(--gold);
  }
  .holder__name { font-weight: 600; }

  .contact {
    position: absolute;
    left: 0;
    right: 0;
    margin: 0;
    font-size: 25px;
    line-height: 40px;
  }
  .contact--numbers { top: 315px; }
  .contact--online  { top: 355px; }
  .contact--address { top: 395px; }
  .contact b { font-weight: 600; }
  .sep { margin: 0 9px; }
</style>
</head>
<body>
<main class="stage">
  <section class="card card--front">
    <div class="brand"><span class="brand__mark"></span><span class="brand__name">Marlow &amp; Quince</span></div>
    <p class="holder"><span class="holder__name">Your Name -</span> Designation</p>
    <p class="contact contact--numbers"><b>p</b> : 123-456-7890<span class="sep">|</span><b>c</b> : 123-456-7890<span class="sep">|</span><b>f</b> : 123-456-7890</p>
    <p class="contact contact--online"><b>e</b> : name@yourwebsite.com<span class="sep">|</span><b>w</b> : www.marlow&amp;quince.com</p>
    <p class="contact contact--address">0000, Street Name, City Name, Country Code.</p>
  </section>

  <section class="card card--back">
    <div class="brand"><span class="brand__mark"></span><span class="brand__name">M &amp; Q</span></div>
  </section>
</main>
</body>
</html>
```